Business Card Design

We are a commercial real estate brokerage in San Francisco, leasing office buildings downtown.
I would like a clean, elegant look. Simple but powerful .

Industry/Entity Type

Business

Contact Information for Business Card

Derek Holloway
lic# 07258143
415.555.0172
derek@velt-commercial.example
velt-commercial.example

```html
<!DOCTYPE html>
<html lang="en">
<head>
<meta charset="utf-8">
<title>Velt Commercial – Business Card</title>
<link rel="stylesheet" href="https://fonts.googleapis.com/css2?family=PT+Sans:wght@400;700&display=swap">
<style>
  :root {
    --backdrop: #ebe7df;
    --card: #ffffff;
    --band: #7889a6;
    --brand: #74849f;
    --name: #7e8ea8;
    --ink: #4a4a4a;
    --icon: #7889a6;
    --skyline: #eef0f3;
  }
  * { margin: 0; padding: 0; box-sizing: border-box; }
  html, body {
    width: 1200px;
    height: 510px;
    overflow: hidden;
    background: var(--backdrop);
    font-family: "PT Sans", sans-serif;
  }
  .card {
    position: absolute;
    top: 132px;
    width: 417px;
    height: 245px;
    background: var(--card);
    border-radius: 12px;
    overflow: hidden;
    box-shadow: 0 2px 6px rgba(0,0,0,0.12);
  }
  .card--front { left: 158px; }
  .card--back { left: 625px; }
  .card__band {
    position: absolute;
    left: 0; right: 0; bottom: 0;
    height: 52px;
    background: var(--band);
  }
  .brand {
    position: absolute;
    left: 40px;
    top: 74px;
    display: flex;
    align-items: center;
    gap: 12px;
    color: var(--brand);
    font-weight: 700;
  }
  .brand__mark {
    width: 34px;
    height: 34px;
    background: var(--brand);
  }
  .brand__name {
    display: flex;
    flex-direction: column;
    line-height: 1;
  }
  .brand__primary { font-size: 30px; letter-spacing: 0.5px; }
  .brand__secondary { font-size: 14px; letter-spacing: 0.3px; margin-top: 2px; }
  .holder-name {
    position: absolute;
    right: 28px;
    bottom: 50px;
    font-size: 19px;
    color: var(--name);
    letter-spacing: 0.3px;
    text-transform: uppercase;
  }
  .skyline {
    position: absolute;
    left: 203px;
    top: 58px;
    width: 207px;
    height: 135px;
    background: linear-gradient(to top, var(--skyline), #f6f7f9);
  }
  .contact {
    position: absolute;
    left: 40px;
    top: 102px;
    list-style: none;
    font-size: 10px;
    color: var(--ink);
  }
  .contact li {
    display: flex;
    align-items: center;
    gap: 4px;
    height: 15.5px;
  }
  .contact__icon {
    width: 8px;
    height: 8px;
    background: var(--icon);
  }
</style>
</head>
<body>
  <section class="card card--front">
    <div class="brand">
      <span class="brand__mark"></span>
      <div class="brand__name">
        <span class="brand__primary">VELT</span>
        <span class="brand__secondary">COMMERCIAL</span>
      </div>
    </div>
    <p class="holder-name">Derek Holloway</p>
    <div class="card__band"></div>
  </section>

  <section class="card card--back">
    <div class="skyline" role="img" aria-label="Faint downtown city skyline illustration"></div>
    <ul class="contact">
      <li><span class="contact__icon"></span>lic# 07258143</li>
      <li><span class="contact__icon"></span>415.555.0172</li>
      <li><span class="contact__icon"></span>derek@velt-commercial.example</li>
      <li><span class="contact__icon"></span>velt-commercial.example</li>
    </ul>
    <div class="card__band"></div>
  </section>
</body>
</html>
```